Website improvements and Adding Functionalities at https://mervo.site/tarnovex

1.Search functionality
2.Payment process functionality
3. Application configuration
4. Registration functionality activation
5. Chat functionality
6.Language switching functionality (Portuguese & French)
7.Bespoke interactive modules
8. Automated web scraping and data synchronisation mechanisms
9. News Page
10.Webinar facilities
11. Basic SEO optimisation
12. Speed and performance optimisation
13. Security configuration
14. Google Analytics integration
15. Cross-browser and mobile testing
16. Website deployment and launch support

Target Market(s)

My target markets are companies, investors, suppliers and professionals with an interest in the Mozambican oil and gas sector

Industry/Entity Type

Oil and Gas

Coding

Coded - Design and coding required

Number of Pages Required

1 page

Requirements
Must have
• Improve the existing page at https://mervo.site/tarnovex and add the following features to it: 1. Search functionality 2. Payment process functionality 3. Application configuration 4. Activation of registration functionality 5. Chat functionality 6. Language switching functionality (Portuguese & French) 7. Bespoke interactive modules 8. Automated web scraping and data synchronisation mechanisms 9. News Page

```html
<!DOCTYPE html>
<html lang="en">
<head>
<meta charset="utf-8">
<title>Tarnovex — Mozambique oil &amp; gas intelligence</title>
<link href="https://fonts.googleapis.com/css2?family=Sora:wght@500;600;700&family=Inter:wght@400;500;600;700&display=swap" rel="stylesheet">
<style>
:root{
  --board:#4a4a4a;
  --night:#1d1236;
  --plum:#2b1a4c;
  --plum-2:#3a2160;
  --card-dark:#2c1d4a;
  --line-dark:rgba(255,255,255,.12);
  --cream:#f6f2ec;
  --paper:#ffffff;
  --ink:#1d1533;
  --muted:#7a7387;
  --muted-light:#b9b1cc;
  --orange:#f26a1b;
  --amber:#f7a23a;
}
*{box-sizing:border-box;margin:0;padding:0}
html,body{width:751px;height:1200px;overflow:hidden;background:var(--board)}
body{font-family:"Inter",sans-serif;color:var(--ink);position:relative}
.a{position:absolute}
.col{position:absolute;top:38px;height:1122px;overflow:hidden;background:var(--cream)}
.col-left{left:36px;width:328px}
.col-right{left:393px;width:322px}
.sec{position:absolute;left:0;width:100%;overflow:hidden}
.dark{background:linear-gradient(160deg,var(--plum) 0%,var(--night) 70%);color:#fff}
.light{background:var(--cream)}
.h{font-family:"Sora",sans-serif;font-weight:600;letter-spacing:-.02em;line-height:1.12}
.hl{background:linear-gradient(90deg,var(--orange),var(--amber));-webkit-background-clip:text;background-clip:text;color:transparent}
.eyebrow{font-size:2.2px;line-height:1;letter-spacing:.12em;text-transform:uppercase;font-weight:600;padding:1px 3px;border-radius:4px;background:rgba(255,255,255,.08);border:.3px solid var(--line-dark);display:inline-block;white-space:nowrap}
.light .eyebrow{background:#ece6dd;border-color:#e0d8cc;color:var(--ink)}
.eyebrow::before{content:"";display:inline-block;width:1.2px;height:1.2px;border-radius:50%;background:var(--orange);margin-right:1.4px;vertical-align:middle}
.p{font-size:2.9px;line-height:1.45;color:var(--muted)}
.dark .p{color:var(--muted-light)}
.btn{font-size:2.6px;font-weight:600;height:7px;padding:0 4px;border-radius:4px;display:inline-flex;align-items:center;white-space:nowrap}
.btn-o{background:var(--orange);color:#fff}
.btn-g{background:#fff;color:var(--ink);border:.3px solid #ddd}
.dark .btn-g{background:rgba(255,255,255,.06);color:#fff;border-color:var(--line-dark)}
.card{background:var(--paper);border-radius:3px;box-shadow:0 1px 4px rgba(40,20,70,.06)}
.panel{background:rgba(255,255,255,.05);border:.3px solid var(--line-dark);border-radius:3px}
.tiny{font-size:2.2px;line-height:1.4}
.mini{font-size:2.6px;line-height:1.35}
.b{font-weight:600}
.ico{width:5px;height:5px;border-radius:50%;background:var(--plum);display:inline-block}
.row{display:flex;align-items:center}
.logo{font-family:"Inter",sans-serif;font-weight:700;font-size:3px;display:flex;align-items:center;gap:1.5px}
.logo i{width:3.4px;height:3.4px;border-radius:50%;background:var(--orange);display:block}
.nav a{color:#d8d0e8;text-decoration:none;font-size:2.4px;margin-right:6px}
.dash{background:#231540;border:.5px solid rgba(255,255,255,.14);border-radius:3px;box-shadow:0 4px 14px rgba(0,0,0,.35)}
.kpi{background:rgba(255,255,255,.05);border-radius:1.5px;padding:1.5px 2px}
.pill{font-size:1.8px;padding:.4px 1.4px;border-radius:3px;background:rgba(242,106,27,.25);color:var(--amber)}
.feat{background:#fff;border:.3px solid #eae4da;border-radius:2px;padding:2px;display:flex;gap:2px}
.feat .ico{width:4px;height:4px;flex:none}
.tag{font-size:2.3px;padding:1px 2px;border-radius:3px;background:rgba(255,255,255,.06);border:.3px solid var(--line-dark);display:flex;align-items:center;gap:1px;white-space:nowrap}
.tag::before{content:"";width:1.6px;height:1.6px;border-radius:50%;border:.3px solid var(--orange)}
.num{font-family:"Sora",sans-serif;font-weight:600}
.step{width:6px;height:6px;border-radius:50%;border:.3px solid rgba(242,106,27,.6);background:rgba(242,106,27,.12);color:var(--amber);font-size:2.1px;display:flex;align-items:center;justify-content:center}
.mod{position:absolute;width:50px;height:44px;background:#fff;border-radius:2px;padding:3px}
.mod .ico{width:6px;height:6px;border-radius:1.5px}
.mod .n{position:absolute;right:3px;top:3px;font-size:1.8px;color:#b4aebc}
.basin{position:absolute;left:58px;width:92px;height:10px;border-radius:2px;background:rgba(255,255,255,.05);border:.3px solid var(--line-dark);padding:1px 2.5px}
.basin .v{position:absolute;right:2.5px;top:3px;font-size:2.2px;color:var(--amber);font-weight:600}
.photo{position:absolute}
.faq{position:absolute;left:89px;width:143px;background:#fff;border:.3px solid #e6dfd4;border-radius:2px;padding:0 4px;font-size:2.6px;font-weight:600;display:flex;align-items:center;justify-content:space-between}
.faq span{font-size:2px;color:var(--muted)}
.price{position:absolute;top:50px;width:66px;height:72px;border-radius:3px;padding:5px}
.price li{list-style:none;font-size:2.1px;margin-bottom:1.8px;display:flex;gap:1.4px;align-items:center}
.price li::before{content:"";width:1.6px;height:1.6px;border-radius:50%;border:.3px solid var(--orange)}
.fcol{position:absolute;top:0;font-size:2.1px;line-height:2.1}
.fcol b{display:block;font-size:1.8px;letter-spacing:.1em;color:var(--muted-light);font-weight:600}
.center{left:0;width:100%;text-align:center}
</style>
</head>
<body>

<!-- LEFT PAGE -->
<div class="col col-left">

  <!-- Hero -->
  <section class="sec dark" style="top:0;height:174px">
    <div class="photo" role="img" aria-label="Offshore gas platform at dusk with glowing orange sky" style="inset:0;background:radial-gradient(ellipse at 92% 10%,rgba(242,106,27,.55),transparent 40%),radial-gradient(ellipse at 75% 60%,rgba(120,70,140,.35),transparent 55%),linear-gradient(160deg,#2e1c50,#1b1134)"></div>
    <div class="a logo" style="left:58px;top:4px"><i></i>Tarnovex</div>
    <nav class="a nav" style="left:121px;top:5.5px"><a>Platform ⌄</a><a>Solutions ⌄</a><a>Markets ⌄</a><a>Insights ⌄</a><a>Pricing ⌄</a></nav>
    <div class="a tiny" style="left:236px;top:6px;color:#d8d0e8">Sign in</div>
    <div class="a btn btn-g" style="left:248px;top:3.5px;height:6px;font-size:2.1px;padding:0 2.5px">Request Demo</div>

    <div class="a eyebrow" style="left:58px;top:31px">Mozambique • Oil &amp; gas intelligence</div>
    <h1 class="a h" style="left:58px;top:39px;width:108px;font-size:11.6px;line-height:1.1">Access Mozambique’s most <span class="hl">trusted oil &amp; gas</span> intelligence platform.</h1>
    <p class="a p" style="left:58px;top:106px;width:97px">Empower investors, operators, suppliers and energy professionals with verified market intelligence, supplier networks, live tenders, legal frameworks and project insights — unified in one enterprise platform.</p>
    <div class="a row" style="left:58px;top:135px;gap:3px"><span class="btn btn-o">Explore Platform →</span><span class="btn btn-g">Request Demo ↗</span></div>
    <div class="a row tiny" style="left:58px;top:149px;gap:5px;color:#cfc7de"><span style="letter-spacing:.1em;color:var(--muted-light)">TRUSTED BY</span><b>Norvane</b><b>Kestral</b><b>Veltaro</b><b>Ostrium</b><b>Lumeno</b><b>Cardeo</b></div>

    <div class="a dash" style="left:173px;top:31px;width:96px;height:87px">
      <div class="a tiny" style="left:4px;top:2.5px;color:var(--amber)">● TARNOVEX • LIVE</div>
      <div class="a tiny" style="left:50px;top:2.5px;width:42px;padding:.5px 2px;border-radius:3px;background:rgba(255,255,255,.06);color:var(--muted-light);font-size:1.8px">⌕ Search projects, tenders, suppliers…</div>
      <div class="a kpi" style="left:4px;top:9px;width:27px"><div class="tiny" style="font-size:1.6px;color:var(--muted-light)">VARUMA BASIN</div><div class="num" style="font-size:3px">$24.8B</div><div style="font-size:1.6px;color:var(--amber)">Active</div></div>
      <div class="a kpi" style="left:34px;top:9px;width:27px"><div class="tiny" style="font-size:1.6px;color:var(--muted-light)">LNG OUTPUT</div><div class="num" style="font-size:3px">13.1 MTPA</div><div style="font-size:1.6px;color:var(--amber)">+3.4%</div></div>
      <div class="a kpi" style="left:64px;top:9px;width:27px"><div class="tiny" style="font-size:1.6px;color:var(--muted-light)">OPEN TENDERS</div><div class="num" style="font-size:3px">42</div><div style="font-size:1.6px;color:var(--amber)">this week</div></div>
      <div class="a" style="left:4px;top:24px;width:88px;height:32px;border-radius:2px;background:rgba(255,255,255,.04)">
        <div class="a tiny b" style="left:3px;top:2px;font-size:1.9px">Production index — Block 1 &amp; Block 4</div>
        <div class="a tiny" style="right:3px;top:2px;font-size:1.8px;color:var(--muted-light)">12M</div>
        <svg class="a" style="left:8px;top:8px" width="72" height="20" viewBox="0 0 72 20"><defs><linearGradient id="g1" x1="0" y1="0" x2="0" y2="1"><stop offset="0" stop-color="#f26a1b" stop-opacity=".55"/><stop offset="1" stop-color="#f26a1b" stop-opacity="0"/></linearGradient></defs><path d="M0 18 L8 15 L14 16 L22 12 L30 13 L38 9 L46 10 L54 6 L62 5 L72 2 L72 20 L0 20Z" fill="url(#g1)"/><path d="M0 18 L8 15 L14 16 L22 12 L30 13 L38 9 L46 10 L54 6 L62 5 L72 2" fill="none" stroke="#f7a23a" stroke-width=".6"/></svg>
      </div>
      <div class="a tiny row" style="left:4px;top:60px;width:88px;justify-content:space-between;font-size:1.8px"><span>Tender — Coral Nereo FLNG maintenance</span><span>$4.2M <span class="pill">Closing</span></span></div>
      <div class="a tiny row" style="left:4px;top:67px;width:88px;justify-content:space-between;font-size:1.8px"><span>Supplier — Varuma Logistics Ltd</span><span>Verified <span class="pill">Member</span></span></div>
      <div class="a tiny row" style="left:4px;top:74px;width:88px;justify-content:space-between;font-size:1.8px"><span>Report — Q2 Local Content Index</span><span>PDF <span class="pill">Updated</span></span></div>
    </div>
    <div class="a dash" style="left:169px;top:27px;width:23px;height:9px;padding:1.5px 2px"><div style="font-size:1.6px;color:var(--muted-light)">PRODUCTION</div><div class="b" style="font-size:2.3px">↑ 8.2%</div></div>
    <div class="a panel row" style="left:241px;top:132px;width:27px;height:8px;border-radius:4px;padding:0 2px;gap:2px;background:rgba(30,18,55,.7)"><span class="ico" style="width:4px;height:4px;background:rgba(242,106,27,.35)"></span><div><div style="font-size:1.6px;color:var(--muted-light)">LIVE TENDERS</div><div class="b" style="font-size:2.2px">42 open</div></div></div>
  </section>

  <!-- Light area -->
  <section class="sec light" style="top:174px;height:244px">
    <div class="photo" role="img" aria-label="Engineer in hard hat facing control room screens" style="left:58px;top:95px;width:106px;height:133px;border-radius:3px;background:linear-gradient(150deg,#3a1f5a,#c0307a 45%,#f07a2a 80%,#2a1a40)"></div>
    <div class="a card" style="left:122px;top:188px;width:49px;height:19px;padding:2.5px">
      <div class="tiny" style="font-size:1.8px;color:var(--muted)">Block 4 — Coral Nereo <span style="color:var(--orange);float:right">Live</span></div>
      <div class="num" style="font-size:4px">3.4 MTPA</div>
      <div class="tiny" style="font-size:1.7px;color:var(--muted)">LNG production capacity</div>
      <div style="margin-top:1.5px;height:1px;background:#eee;border-radius:1px"><div style="width:70%;height:1px;background:var(--orange)"></div></div>
    </div>

    <div class="a eyebrow" style="left:173px;top:96px">The platform</div>
    <h2 class="a h" style="left:173px;top:103px;width:95px;font-size:7.4px;line-height:1.4">Everything you need to navigate Mozambique’s energy market.</h2>
    <p class="a p" style="left:173px;top:138px;width:92px;font-size:2.5px">One workspace for intelligence, due diligence and execution — from upstream exploration to LNG export.</p>

    <div class="a feat" style="left:173px;top:148px;width:47px;height:14px"><span class="ico"></span><div><div class="tiny b">Industry intelligence</div><div class="tiny" style="font-size:1.8px;color:var(--muted)">Verified market data, refreshed daily.</div></div></div>
    <div class="a feat" style="left:223px;top:148px;width:46px;height:14px"><span class="ico"></span><div><div class="tiny b">Supplier network</div><div class="tiny" style="font-size:1.8px;color:var(--muted)">2,500+ vetted local &amp; global suppliers.</div></div></div>
    <div class="a feat" style="left:173px;top:165px;width:47px;height:14px"><span class="ico"></span><div><div class="tiny b">Tender opportunities</div><div class="tiny" style="font-size:1.8px;color:var(--muted)">Real-time tender feed with alerts.</div></div></div>
    <div class="a feat" style="left:223px;top:165px;width:46px;height:14px"><span class="ico"></span><div><div class="tiny b">Legal framework</div><div class="tiny" style="font-size:1.8px;color:var(--muted)">Petroleum laws, contracts, fiscal terms.</div></div></div>
    <div class="a feat" style="left:173px;top:182px;width:47px;height:14px"><span class="ico"></span><div><div class="tiny b">Project database</div><div class="tiny" style="font-size:1.8px;color:var(--muted)">Onshore, offshore, midstream coverage.</div></div></div>
    <div class="a feat" style="left:223px;top:182px;width:46px;height:14px"><span class="ico"></span><div><div class="tiny b">Investor insights</div><div class="tiny" style="font-size:1.8px;color:var(--muted)">Models, ownership maps, deal flow.</div></div></div>
    <div class="a feat" style="left:173px;top:199px;width:47px;height:14px"><span class="ico"></span><div><div class="tiny b">Ownership data</div><div class="tiny" style="font-size:1.8px;color:var(--muted)">Beneficial owners &amp; corporate structures.</div></div></div>
    <div class="a feat" style="left:223px;top:199px;width:46px;height:14px"><span class="ico"></span><div><div class="tiny b">Local content</div><div class="tiny" style="font-size:1.8px;color:var(--muted)">Compliance tracking &amp; reporting.</div></div></div>
    <div class="a row" style="left:173px;top:220px;gap:3px"><span class="btn btn-o">View Platform →</span><span class="btn btn-g">Book a walkthrough ↗</span></div>
  </section>

  <!-- Trust card -->
  <div class="a card" style="left:58px;top:163px;width:211px;height:72px;border-radius:4px;box-shadow:0 3px 12px rgba(40,20,70,.12)">
    <div class="a eyebrow" style="left:8px;top:8px;background:none;border:0;color:var(--ink)">Industry trust</div>
    <h3 class="a h" style="left:8px;top:15px;width:100px;font-size:5.4px">Trusted by Mozambique’s energy ecosystem.</h3>
    <p class="a p" style="left:126px;top:19px;width:75px;font-size:2.3px">From majors and EPC contractors to government agencies and investors — Tarnovex is the source of truth used across the value chain.</p>
    <div class="a row" style="left:8px;top:40px;gap:0">
      <div style="width:40px"><div class="num" style="font-size:5.4px">500+</div><div style="font-size:1.7px;letter-spacing:.1em;color:var(--muted)">REGISTERED COMPANIES</div></div>
      <div style="width:40px"><div class="num" style="font-size:5.4px">2,500+</div><div style="font-size:1.7px;letter-spacing:.1em;color:var(--muted)">VERIFIED SUPPLIERS</div></div>
      <div style="width:40px"><div class="num" style="font-size:5.4px">1,000+</div><div style="font-size:1.7px;letter-spacing:.1em;color:var(--muted)">INDUSTRY REPORTS</div></div>
      <div style="width:40px"><div class="num" style="font-size:5.4px">150+</div><div style="font-size:1.7px;letter-spacing:.1em;color:var(--muted)">LIVE PROJECTS</div></div>
      <div style="width:40px"><div class="num" style="font-size:5.4px">95%</div><div style="font-size:1.7px;letter-spacing:.1em;color:var(--muted)">CUSTOMER SATISFACTION</div></div>
    </div>
    <div class="a row" style="left:8px;top:59px;width:196px;justify-content:space-between;font-size:2.6px;font-weight:600;color:#9a93a6"><span>Norvane</span><span>Kestral</span><span>Veltaro</span><span>Ostrium</span><span>Lumeno</span><span>Miyaro</span><span>Cardeo</span><span>Brisal</span><span>Halden Bank</span><span>Petrova</span></div>
  </div>

  <!-- Real-time intelligence -->
  <section class="sec dark" style="top:418px;height:395px;background:radial-gradient(ellipse at 100% 0%,rgba(242,106,27,.35),transparent 35%),linear-gradient(180deg,#241540,#1c1236 60%,#2a1748)">
    <div class="a center" style="top:20px"><span class="eyebrow">Core platform feature</span></div>
    <h2 class="a h center" style="top:28px;font-size:9.4px;line-height:1.15">Real-Time Industry<br>Intelligence<br><span class="hl">powered by automated<br>data synchronization</span></h2>
    <p class="a p" style="left:106px;width:116px;top:76px;text-align:center;font-size:2.6px">Tarnovex continuously gathers, validates and synchronizes information from trusted sources across Mozambique’s oil &amp; gas sector — delivering accurate, structured, up-to-date intelligence in one secure platform.</p>

    <svg class="a" style="left:58px;top:108px" width="112" height="110" viewBox="0 0 112 110">
      <defs><radialGradient id="core"><stop offset="0" stop-color="#f7a23a" stop-opacity=".9"/><stop offset=".55" stop-color="#f26a1b" stop-opacity=".35"/><stop offset="1" stop-color="#f26a1b" stop-opacity="0"/></radialGradient></defs>
      <g stroke="rgba(242,106,27,.35)" stroke-width=".3">
        <line x1="56" y1="55" x2="56" y2="8"/><line x1="56" y1="55" x2="20" y2="15"/><line x1="56" y1="55" x2="90" y2="15"/><line x1="56" y1="55" x2="12" y2="32"/><line x1="56" y1="55" x2="100" y2="32"/><line x1="56" y1="55" x2="8" y2="55"/><line x1="56" y1="55" x2="104" y2="55"/><line x1="56" y1="55" x2="12" y2="78"/><line x1="56" y1="55" x2="100" y2="78"/><line x1="56" y1="55" x2="28" y2="94"/><line x1="56" y1="55" x2="84" y2="94"/><line x1="56" y1="55" x2="56" y2="100"/>
      </g>
      <circle cx="56" cy="55" r="28" fill="url(#core)"/>
      <circle cx="56" cy="55" r="15" fill="#3a2160" stroke="#f26a1b" stroke-width=".5"/>
      <text x="56" y="54" text-anchor="middle" fill="#fff" font-size="2.4" font-family="Inter" font-weight="600">Tarnovex</text>
      <text x="56" y="57" text-anchor="middle" fill="#fff" font-size="2.2" font-family="Inter">Intelligence Engine</text>
      <text x="56" y="60.5" text-anchor="middle" fill="#f7a23a" font-size="1.8" font-family="Inter">● Live sync</text>
    </svg>
    <div class="a tag" style="left:104px;top:112px;font-size:1.8px">Government Portals</div>
    <div class="a tag" style="left:70px;top:118px;font-size:1.8px">Offshore Developments</div>
    <div class="a tag" style="left:130px;top:118px;font-size:1.8px">Energy Ministry Releases</div>
    <div class="a tag" style="left:66px;top:135px;font-size:1.8px">LNG Projects</div>
    <div class="a tag" style="left:142px;top:135px;font-size:1.8px">Regulatory Authorities</div>
    <div class="a tag" style="left:60px;top:157px;font-size:1.8px">Legal Publications</div>
    <div class="a tag" style="left:146px;top:157px;font-size:1.8px">National Oil Companies</div>
    <div class="a tag" style="left:66px;top:180px;font-size:1.8px">Industry News</div>
    <div class="a tag" style="left:140px;top:180px;font-size:1.8px">International Operators</div>
    <div class="a tag" style="left:82px;top:196px;font-size:1.8px">Supplier Databases</div>
    <div class="a tag" style="left:126px;top:196px;font-size:1.8px">EPC Contractors</div>
    <div class="a tag" style="left:108px;top:202px;font-size:1.8px">Tender Portals</div>
    <div class="a row" style="left:92px;top:211px;gap:2px"><span class="tag" style="font-size:1.8px">Connected</span><span class="tag" style="font-size:1.8px">Syncing</span><span class="tag" style="font-size:1.8px">Verified</span></div>

    <div class="a" style="left:173px;top:128px;display:grid;grid-template-columns:45px 45px;gap:2px 2px">
      <span class="tag">Automated Web Scraping</span><span class="tag">AI-Powered Data Validation</span>
      <span class="tag">Scheduled Synchronization</span><span class="tag">Duplicate Detection</span>
      <span class="tag">Multi-Source Aggregation</span><span class="tag">Real-Time Updates</span>
      <span class="tag">Intelligent Categorization</span><span class="tag">Source Verification</span>
      <span class="tag">Tender Monitoring</span><span class="tag">Regulatory Updates</span>
    </div>
    <div class="a row" style="left:173px;top:178px;gap:3px"><span class="btn btn-o">See How It Works →</span><span class="tiny" style="color:var(--muted-light)">● Last sync · 2 minutes ago</span></div>

    <div class="a panel row" style="left:58px;top:225px;width:211px;height:19px;border-radius:4px;justify-content:space-around;text-align:center">
      <div><div class="num hl" style="font-size:5.6px">25+</div><div style="font-size:1.6px;letter-spacing:.1em;color:var(--muted-light)">CONNECTED SOURCES</div></div>
      <div><div class="num" style="font-size:5.6px">15,000+</div><div style="font-size:1.6px;letter-spacing:.1em;color:var(--muted-light)">INDUSTRY RECORDS</div></div>
      <div><div class="num hl" style="font-size:5.6px">500+</div><div style="font-size:1.6px;letter-spacing:.1em;color:var(--muted-light)">SYNCED MONTHLY</div></div>
      <div><div class="num hl" style="font-size:5.6px">100%</div><div style="font-size:1.6px;letter-spacing:.1em;color:var(--muted-light)">VERIFIED WORKFLOW</div></div>
      <div><div class="num hl" style="font-size:5.6px">24/7</div><div style="font-size:1.6px;letter-spacing:.1em;color:var(--muted-light)">LIVE DATA</div></div>
    </div>

    <div class="a eyebrow" style="left:58px;top:259px">Process</div>
    <h3 class="a h" style="left:58px;top:267px;font-size:5px">From raw signals to verified intelligence</h3>
    <div class="a tiny" style="left:235px;top:270px;font-size:1.8px;color:var(--muted-light)">Auto-orchestrated · Continuous</div>
    <div class="a" style="left:62px;top:282px;width:200px;height:.4px;background:rgba(242,106,27,.35)"></div>
    <div class="a row" style="left:58px;top:279px;width:211px;justify-content:space-between;text-align:center">
      <div style="width:30px"><div class="step" style="margin:0 auto">01</div><div class="tiny b" style="margin-top:2px">Collect Data</div><div style="font-size:1.6px;color:var(--muted-light)">Scrape trusted portals</div></div>
      <div style="width:30px"><div class="step" style="margin:0 auto">02</div><div class="tiny b" style="margin-top:2px">Clean &amp; Validate</div><div style="font-size:1.6px;color:var(--muted-light)">Normalize + dedupe</div></div>
      <div style="width:30px"><div class="step" style="margin:0 auto">03</div><div class="tiny b" style="margin-top:2px">AI Classification</div><div style="font-size:1.6px;color:var(--muted-light)">Tag, score, route</div></div>
      <div style="width:30px"><div class="step" style="margin:0 auto">04</div><div class="tiny b" style="margin-top:2px">Synchronize DB</div><div style="font-size:1.6px;color:var(--muted-light)">Versioned writes</div></div>
      <div style="width:30px"><div class="step" style="margin:0 auto">05</div><div class="tiny b" style="margin-top:2px">Publish</div><div style="font-size:1.6px;color:var(--muted-light)">Distribute live</div></div>
      <div style="width:30px"><div class="step" style="margin:0 auto">06</div><div class="tiny b" style="margin-top:2px">Notify</div><div style="font-size:1.6px;color:var(--muted-light)">Alert subscribers</div></div>
    </div>

    <div class="a panel" style="left:58px;top:307px;width:140px;height:67px;border-radius:4px">
      <div class="a tiny b" style="left:4px;top:3px">▣ Live Intelligence Feed</div>
      <div class="a pill" style="right:4px;top:3px">● AUTO SYNC · ON</div>
      <div class="a" style="left:4px;top:10px;width:132px">
        <div class="row" style="height:10.5px;border-bottom:.3px solid var(--line-dark);gap:2px"><span class="ico" style="width:3px;height:3px;background:rgba(242,106,27,.4)"></span><div style="flex:1"><div class="tiny">Tender · Varuma LNG balance-of-plant EPC</div><div style="font-size:1.5px;color:var(--muted-light)">Tender Portal</div></div><span class="tag" style="font-size:1.5px">NEW</span></div>
        <div class="row" style="height:10.5px;border-bottom:.3px solid var(--line-dark);gap:2px"><span class="ico" style="width:3px;height:3px;background:rgba(242,106,27,.4)"></span><div style="flex:1"><div class="tiny">Supplier verified · Ossara Marine Services</div><div style="font-size:1.5px;color:var(--muted-light)">Supplier DB</div></div><span class="tag" style="font-size:1.5px">VERIFIED</span></div>
        <div class="row" style="height:10.5px;border-bottom:.3px solid var(--line-dark);gap:2px"><span class="ico" style="width:3px;height:3px;background:rgba(242,106,27,.4)"></span><div style="flex:1"><div class="tiny">Regulation update · Local Content Decree 12/2026</div><div style="font-size:1.5px;color:var(--muted-light)">Legal</div></div><span class="tag" style="font-size:1.5px">UPDATED</span></div>
        <div class="row" style="height:10.5px;border-bottom:.3px solid var(--line-dark);gap:2px"><span class="ico" style="width:3px;height:3px;background:rgba(242,106,27,.4)"></span><div style="flex:1"><div class="tiny">Coral Nereo FLNG · 4th cargo dispatched</div><div style="font-size:1.5px;color:var(--muted-light)">Industry News</div></div><span class="tag" style="font-size:1.5px">LIVE</span></div>
        <div class="row" style="height:10.5px;gap:2px"><span class="ico" style="width:3px;height:3px;background:rgba(242,106,27,.4)"></span><div style="flex:1"><div class="tiny">Block 1 development resumption schedule</div><div style="font-size:1.5px;color:var(--muted-light)">Operator</div></div><span class="tag" style="font-size:1.5px">WATCH</span></div>
      </div>
    </div>
    <div class="a panel" style="left:202px;top:308px;width:67px;height:30px;border-radius:4px;padding:3px">
      <div class="tiny b">◯ Source Verification</div>
      <div class="tiny" style="font-size:1.7px;color:var(--muted-light);margin-top:1.5px;line-height:1.75">
        <div class="row" style="justify-content:space-between">Energy ministry portal<span style="color:var(--amber)">◯ Verified</span></div>
        <div class="row" style="justify-content:space-between">Petroleum regulator<span style="color:var(--amber)">◯ Verified</span></div>
        <div class="row" style="justify-content:space-between">Norvane<span style="color:var(--amber)">◯ Verified</span></div>
        <div class="row" style="justify-content:space-between">Veltaro<span style="color:var(--amber)">◯ Verified</span></div>
        <div class="row" style="justify-content:space-between">Lumeno Varuma<span style="color:var(--amber)">◯ Verified</span></div>
      </div>
    </div>
    <div class="a panel" style="left:202px;top:343px;width:67px;height:21px;border-radius:4px;padding:3px">
      <div class="tiny b">⌕ Smart Filters</div>
      <div class="row" style="flex-wrap:wrap;gap:1px;margin-top:2px">
        <span class="tag" style="font-size:1.5px">Tenders</span><span class="tag" style="font-size:1.5px">EPC</span><span class="tag" style="font-size:1.5px">LNG</span><span class="tag" style="font-size:1.5px">Offshore</span><span class="tag" style="font-size:1.5px">Regulatory</span><span class="tag" style="font-size:1.5px">Suppliers</span><span class="tag" style="font-size:1.5px">News</span>
      </div>
    </div>
  </section>

  <!-- Eight modules -->
  <section class="sec light" style="top:813px;height:160px;background:#f2eee7">
    <div class="a eyebrow" style="left:58px;top:20px;background:none;border:0">Core solutions</div>
    <h2 class="a h" style="left:58px;top:29px;width:80px;font-size:7.4px">Eight modules. <span class="hl">One intelligence layer.</span></h2>
    <p class="a p" style="left:204px;top:33px;width:64px;font-size:2.2px">Designed for oil companies, EPC contractors, investors, suppliers and government agencies operating in Mozambique.</p>

    <div class="mod" style="left:58px;top:53px"><span class="n">01</span><span class="ico"></span><div class="mini b" style="margin-top:6px">Industry Intelligence</div><div class="tiny" style="color:var(--muted);margin-top:1px">Daily-refreshed market signals across upstream, midstream and LNG.</div></div>
    <div class="mod" style="left:112px;top:53px"><span class="n">02</span><span class="ico"></span><div class="mini b" style="margin-top:6px">Projects Database</div><div class="tiny" style="color:var(--muted);margin-top:1px">150+ live projects with operators, partners, value and status.</div></div>
    <div class="mod" style="left:166px;top:53px"><span class="n">03</span><span class="ico"></span><div class="mini b" style="margin-top:6px">Supplier Network</div><div class="tiny" style="color:var(--muted);margin-top:1px">Vetted directory with capabilities, certifications and contacts.</div></div>
    <div class="mod" style="left:219px;top:53px"><span class="n">04</span><span class="ico"></span><div class="mini b" style="margin-top:6px">Tender Hub</div><div class="tiny" style="color:var(--muted);margin-top:1px">Real-time tender feed, smart filters, automated alerts.</div></div>
    <div class="mod" style="left:58px;top:101px;height:40px"><span class="n">05</span><span class="ico"></span><div class="mini b" style="margin-top:6px">Legal Framework</div><div class="tiny" style="color:var(--muted);margin-top:1px">Petroleum law, fiscal terms, model contracts and rulings.</div></div>
    <div class="mod" style="left:112px;top:101px;height:40px"><span class="n">06</span><span class="ico"></span><div class="mini b" style="margin-top:6px">Market Reports</div><div class="tiny" style="color:var(--muted);margin-top:1px">Analyst-grade reports on basins, sectors and themes.</div></div>
    <div class="mod" style="left:166px;top:101px;height:40px"><span class="n">07</span><span class="ico"></span><div class="mini b" style="margin-top:6px">Investor Center</div><div class="tiny" style="color:var(--muted);margin-top:1px">Deal flow, ownership maps, capex pipelines.</div></div>
    <div class="mod" style="left:219px;top:101px;height:40px"><span class="n">08</span><span class="ico"></span><div class="mini b" style="margin-top:6px">Compliance Tools</div><div class="tiny" style="color:var(--muted);margin-top:1px">Local content tracking, ESG, sanctions screening.</div></div>
  </section>

  <!-- Map -->
  <section class="sec dark" style="top:973px;height:149px">
    <div class="a eyebrow" style="left:58px;top:20px">Live intelligence map</div>
    <h2 class="a h" style="left:58px;top:29px;width:100px;font-size:7.4px;line-height:1.4">Every basin, block &amp; terminal — <span class="hl">mapped.</span></h2>
    <p class="a p" style="left:58px;top:52px;width:92px;font-size:2.4px">Hover any project to reveal operator, capex, status and partners. Drill into offshore blocks, LNG facilities, ports and pipelines across Mozambique.</p>
    <div class="basin" style="top:70px"><div style="font-size:1.5px;color:var(--muted-light)">VELTARO</div><div class="tiny b">Varuma Basin</div><span class="v">$24.8B</span></div>
    <div class="basin" style="top:83px"><div style="font-size:1.5px;color:var(--muted-light)">LUMENO</div><div class="tiny b">Block 4 — Coral Nereo</div><span class="v">$9.0B</span></div>
    <div class="basin" style="top:96px;border-color:rgba(242,106,27,.5);background:rgba(242,106,27,.12)"><div style="font-size:1.5px;color:var(--muted-light)">KESTRAL</div><div class="tiny b">Sendo / Talumi</div><span class="v">$2.3B</span></div>
    <div class="basin" style="top:109px"><div style="font-size:1.5px;color:var(--muted-light)">PORTRA</div><div class="tiny b">Cabela Terminal</div><span class="v">$0.6B</span></div>
    <div class="basin" style="top:122px"><div style="font-size:1.5px;color:var(--muted-light)">PETROVA</div><div class="tiny b">Lindavo Port</div><span class="v">$1.2B</span></div>
    <div class="a panel" role="img" aria-label="Map of Mozambique's coastline with project locations" style="left:159px;top:25px;width:110px;height:98px;border-radius:4px;background:radial-gradient(ellipse at 55% 45%,rgba(242,106,27,.25),transparent 45%),rgba(255,255,255,.03)"></div>
    <div class="a panel" style="left:163px;top:108px;width:24px;height:11px;padding:1.5px 2px;background:rgba(30,18,55,.9)"><div style="font-size:1.5px;color:var(--muted-light)">NOW SHOWING</div><div class="tiny b">Sendo / Talumi</div><div style="font-size:1.5px;color:var(--muted-light)">Kestral • $2.3B</div></div>
  </section>
</div>

<!-- RIGHT PAGE -->
<div class="col col-right">

  <section class="sec light" style="top:0;height:130px;background:#f6f3ee">
    <div class="a eyebrow" style="left:57px;top:24px;background:none;border:0">Why Tarnovex</div>
    <h2 class="a h" style="left:57px;top:32px;width:120px;font-size:7.4px">Built for decisions that move billions.</h2>
    <div class="a card" style="left:57px;top:56px;width:66px;height:55px;padding:5px"><div class="num hl" style="font-size:10px">01</div><span class="ico" style="margin-top:2px"></span><div class="mini b" style="margin-top:4px">Verified industry data</div><div class="tiny" style="color:var(--muted);margin-top:1px">Every record passes a multi-step validation by our research team — sources, ownership, and cross-references.</div></div>
    <div class="a card" style="left:127px;top:56px;width:66px;height:55px;padding:5px"><div class="num hl" style="font-size:10px">02</div><span class="ico" style="margin-top:2px"></span><div class="mini b" style="margin-top:4px">Updated daily</div><div class="tiny" style="color:var(--muted);margin-top:1px">Live ingestion of tenders, regulatory filings, project milestones and market signals across Mozambique.</div></div>
    <div class="a card" style="left:198px;top:56px;width:66px;height:55px;padding:5px"><div class="num hl" style="font-size:10px">03</div><span class="ico" style="margin-top:2px"></span><div class="mini b" style="margin-top:4px">AI-powered search</div><div class="tiny" style="color:var(--muted);margin-top:1px">Natural-language search across millions of data points — ask anything about projects, suppliers or capex.</div></div>
  </section>

  <section class="sec dark" style="top:130px;height:93px">
    <div class="a eyebrow" style="left:57px;top:21px">How it works</div>
    <h2 class="a h" style="left:57px;top:29px;font-size:7.2px">From signup to insight in minutes.</h2>
    <p class="a p" style="left:200px;top:29px;width:66px;font-size:2.2px">A frictionless onboarding designed for enterprise teams across operations, BD and procurement.</p>
    <div class="a" style="left:63px;top:55px;width:180px;border-top:.4px dashed rgba(255,255,255,.2)"></div>
    <div class="a step" style="left:57px;top:50px;width:11px;height:11px;border-radius:3px;font-size:3px;background:#2c1b4a">01</div>
    <div class="a step" style="left:100px;top:50px;width:11px;height:11px;border-radius:3px;font-size:3px;background:#2c1b4a">02</div>
    <div class="a step" style="left:142px;top:50px;width:11px;height:11px;border-radius:3px;font-size:3px;background:#2c1b4a">03</div>
    <div class="a step" style="left:185px;top:50px;width:11px;height:11px;border-radius:3px;font-size:3px;background:#2c1b4a">04</div>
    <div class="a step" style="left:227px;top:50px;width:11px;height:11px;border-radius:3px;font-size:3px;background:#2c1b4a">05</div>
    <div class="a" style="left:57px;top:65px;width:38px"><div class="mini b">Register</div><div class="tiny" style="color:var(--muted-light)">Create your corporate account in minutes.</div></div>
    <div class="a" style="left:100px;top:65px;width:38px"><div class="mini b">Subscribe</div><div class="tiny" style="color:var(--muted-light)">Choose the plan that fits your team.</div></div>
    <div class="a" style="left:142px;top:65px;width:38px"><div class="mini b">Access platform</div><div class="tiny" style="color:var(--muted-light)">Unified workspace, single sign-on.</div></div>
    <div class="a" style="left:185px;top:65px;width:38px"><div class="mini b">Search intelligence</div><div class="tiny" style="color:var(--muted-light)">Ask anything. Filter everything.</div></div>
    <div class="a" style="left:227px;top:65px;width:40px"><div class="mini b">Grow business</div><div class="tiny" style="color:var(--muted-light)">Win tenders, find partners, close deals.</div></div>
  </section>

  <section class="sec light" style="top:223px;height:308px;background:linear-gradient(180deg,#f6f3ee,#efebe4)">
    <div class="a eyebrow" style="left:57px;top:29px;background:none;border:0">Live platform</div>
    <h2 class="a h" style="left:57px;top:37px;width:85px;font-size:7.4px">A workspace that thinks like an analyst.</h2>
    <p class="a p" style="left:57px;top:54px;width:78px;font-size:2.3px">Smart search, contextual filters, saved views, alerts and an AI assistant — designed for analysts, procurement leads and decision makers.</p>
    <div class="a tiny" style="left:57px;top:71px;line-height:2.7;color:#4a4358">
      <div>◯&nbsp; Advanced global search with filters</div>
      <div>◯&nbsp; Saved searches &amp; favorites</div>
      <div>◯&nbsp; Tender alerts &amp; email notifications</div>
      <div>◯&nbsp; AI assistant for natural-language queries</div>
      <div>◯&nbsp; Personalized dashboards by role</div>
    </div>
    <div class="a dash" style="left:155px;top:19px;width:109px;height:87px;border:2px solid #3a2a5a">
      <div class="a tiny" style="left:4px;top:2.5px;color:var(--amber)">● TARNOVEX • LIVE</div>
      <div class="a tiny" style="left:60px;top:2.5px;width:44px;padding:.5px 2px;border-radius:3px;background:rgba(255,255,255,.06);color:var(--muted-light);font-size:1.8px">⌕ Search projects, tenders, suppliers…</div>
      <div class="a kpi" style="left:4px;top:10px;width:31px"><div style="font-size:1.6px;color:var(--muted-light)">VARUMA BASIN</div><div class="num" style="font-size:3px">$24.8B</div><div style="font-size:1.6px;color:var(--amber)">Active</div></div>
      <div class="a kpi" style="left:38px;top:10px;width:31px"><div style="font-size:1.6px;color:var(--muted-light)">LNG OUTPUT</div><div class="num" style="font-size:3px">13.1 MTPA</div><div style="font-size:1.6px;color:var(--amber)">+3.4%</div></div>
      <div class="a kpi" style="left:72px;top:10px;width:31px"><div style="font-size:1.6px;color:var(--muted-light)">OPEN TENDERS</div><div class="num" style="font-size:3px">42</div><div style="font-size:1.6px;color:var(--amber)">this week</div></div>
      <div class="a" style="left:4px;top:26px;width:99px;height:30px;border-radius:2px;background:rgba(255,255,255,.04)">
        <div class="a tiny b" style="left:3px;top:2px;font-size:1.9px">Production index — Block 1 &amp; Block 4</div>
        <div class="a tiny" style="right:3px;top:2px;font-size:1.8px;color:var(--muted-light)">12M</div>
        <svg class="a" style="left:10px;top:8px" width="80" height="19" viewBox="0 0 72 20" preserveAspectRatio="none"><defs><linearGradient id="g2" x1="0" y1="0" x2="0" y2="1"><stop offset="0" stop-color="#f26a1b" stop-opacity=".55"/><stop offset="1" stop-color="#f26a1b" stop-opacity="0"/></linearGradient></defs><path d="M0 18 L8 15 L14 16 L22 12 L30 13 L38 9 L46 10 L54 6 L62 5 L72 2 L72 20 L0 20Z" fill="url(#g2)"/><path d="M0 18 L8 15 L14 16 L22 12 L30 13 L38 9 L46 10 L54 6 L62 5 L72 2" fill="none" stroke="#f7a23a" stroke-width=".6"/></svg>
      </div>
      <div class="a tiny row" style="left:4px;top:61px;width:99px;justify-content:space-between;font-size:1.8px"><span>Tender — Coral Nereo FLNG maintenance</span><span>$4.2M <span class="pill">Closing</span></span></div>
      <div class="a tiny row" style="left:4px;top:69px;width:99px;justify-content:space-between;font-size:1.8px"><span>Supplier — Varuma Logistics Ltd</span><span>Verified <span class="pill">Member</span></span></div>
      <div class="a tiny row" style="left:4px;top:77px;width:99px;justify-content:space-between;font-size:1.8px"><span>Report — Q2 Local Content Index</span><span>PDF <span class="pill">Updated</span></span></div>
    </div>

    <div class="a eyebrow" style="left:57px;top:145px;background:none;border:0">News &amp; insights</div>
    <h2 class="a h" style="left:57px;top:154px;width:190px;font-size:7.4px">Bio-based, bold, and built for the Mozambique market.</h2>
    <div class="a tiny" style="left:246px;top:162px;color:var(--orange)">View all insights →</div>

    <div class="a card" style="left:57px;top:176px;width:66px;height:112px;overflow:hidden">
      <div class="photo" role="img" aria-label="Gas processing plant venting steam under a purple sunset" style="left:0;top:0;width:66px;height:70px;background:linear-gradient(180deg,#3b2150,#8a3a55 45%,#e0733a 70%,#2a1a30)"></div>
      <div class="a pill" style="left:4px;top:64px;background:var(--orange);color:#fff">FEATURED</div>
      <div class="a tiny" style="left:4px;top:74px;font-size:1.8px;color:var(--muted)">June 22, 2026 • Market Outlook</div>
      <div class="a h" style="left:4px;top:78px;width:58px;font-size:3.6px;line-height:1.3">Varuma 2026: how Mozambique becomes the world’s third largest LNG exporter.</div>
      <div class="a tiny" style="left:4px;top:99px;width:58px;font-size:1.8px;color:var(--muted)">A deep dive into FID timelines, partner alignment and shipping capacity in the Varuma Basin.</div>
    </div>
    <div class="a card" style="left:127px;top:176px;width:66px;height:59px;overflow:hidden">
      <div class="photo" role="img" aria-label="LNG storage tanks at twilight" style="left:0;top:0;width:66px;height:33px;background:linear-gradient(180deg,#3a2a8a,#8a5ad0 45%,#3a2a6a)"></div>
      <div class="a pill" style="left:2px;top:2px;background:#fff;color:var(--ink)">TENDERS</div>
      <div class="a tiny" style="left:4px;top:37px;font-size:1.7px;color:var(--muted)">June 2026</div>
      <div class="a tiny b" style="left:4px;top:40px;width:58px">Q3 tender wave: $1.4B in upcoming opportunities you can’t miss.</div>
      <div class="a tiny" style="left:4px;top:50px;color:var(--orange)">Read post →</div>
    </div>
    <div class="a card" style="left:198px;top:176px;width:66px;height:59px;overflow:hidden">
      <div class="photo" role="img" aria-label="Aerial view of an industrial coastal facility at dawn" style="left:0;top:0;width:66px;height:33px;background:linear-gradient(180deg,#c98a5a,#8a6a5a 50%,#4a3a3a)"></div>
      <div class="a pill" style="left:2px;top:2px;background:#fff;color:var(--ink)">LOCAL CONTENT</div>
      <div class="a tiny" style="left:4px;top:37px;font-size:1.7px;color:var(--muted)">June 2026</div>
      <div class="a tiny b" style="left:4px;top:40px;width:58px">Inside the new local content rulebook — what changes for suppliers.</div>
      <div class="a tiny" style="left:4px;top:50px;color:var(--orange)">Read post →</div>
    </div>
  </section>

  <section class="sec light" style="top:531px;height:142px;background:#f6f3ee">
    <div class="a eyebrow" style="left:57px;top:20px;background:none;border:0">Membership</div>
    <h2 class="a h" style="left:57px;top:29px;width:110px;font-size:7.4px">Premium access, priced for outcomes.</h2>
    <div class="price card" style="left:57px">
      <div style="font-size:1.8px;letter-spacing:.1em;font-weight:600">STARTER</div>
      <div class="num" style="font-size:7px;margin-top:1px">$490 <span style="font-size:1.8px;color:var(--muted);font-family:Inter">/ month</span></div>
      <div class="tiny" style="color:var(--muted);margin-bottom:4px">for individuals &amp; consultants</div>
      <ul><li>Industry intelligence</li><li>Tender alerts</li><li>Supplier directory (read-only)</li><li>5 saved searches</li></ul>
      <div class="btn btn-g" style="position:absolute;left:5px;right:5px;bottom:8px;justify-content:center;height:6px;font-size:2.1px">Choose Starter →</div>
    </div>
    <div class="price" style="left:127px;background:linear-gradient(160deg,#4a2870,#251543);color:#fff;box-shadow:0 4px 12px rgba(40,20,70,.3)">
      <div class="a pill" style="right:3px;top:3px;background:var(--orange);color:#fff">MOST POPULAR</div>
      <div style="font-size:1.8px;letter-spacing:.1em;font-weight:600">PROFESSIONAL</div>
      <div class="num" style="font-size:7px;margin-top:1px">$1,890 <span style="font-size:1.8px;color:var(--muted-light);font-family:Inter">/ month</span></div>
      <div class="tiny" style="color:var(--muted-light);margin-bottom:4px">for growing teams</div>
      <ul><li>Everything in Starter</li><li>Projects &amp; ownership data</li><li>Legal framework library</li><li>AI assistant</li><li>Unlimited saved searches</li></ul>
      <div class="btn btn-o" style="position:absolute;left:5px;right:5px;bottom:8px;justify-content:center;height:6px;font-size:2.1px">Start free trial →</div>
    </div>
    <div class="price card" style="left:198px">
      <div style="font-size:1.8px;letter-spacing:.1em;font-weight:600">ENTERPRISE</div>
      <div class="h" style="font-size:7px;margin-top:1px">Custom</div>
      <div class="tiny" style="color:var(--muted);margin-bottom:4px">for majors, EPC &amp; gov agencies</div>
      <ul><li>Everything in Pro</li><li>Dedicated analyst</li><li>API access</li><li>SSO &amp; audit logs</li><li>Custom dashboards</li></ul>
      <div class="btn btn-g" style="position:absolute;left:5px;right:5px;bottom:8px;justify-content:center;height:6px;font-size:2.1px">Choose Enterprise →</div>
    </div>
  </section>

  <section class="sec dark" style="top:673px;height:110px">
    <div class="a center" style="top:19px;height:4px"><span class="eyebrow">What clients say</span></div>
    <blockquote class="a" style="left:100px;width:122px;top:29px;text-align:center;font-family:'Sora',sans-serif;font-weight:500;font-size:5.6px;line-height:1.5;letter-spacing:-.01em"><span style="color:var(--orange)">“</span>Tarnovex is the first platform that finally treats Mozambique’s energy sector as the world-class market it is. The depth, the verification and the speed are simply unmatched.<span style="color:var(--orange)">”</span></blockquote>
    <div class="a center" style="top:78px;color:var(--amber);font-size:2.6px;letter-spacing:.4px">★★★★★</div>
    <div class="a tiny b center" style="top:82px">Lina Maravé</div>
    <div class="a center" style="top:86px;font-size:1.7px;letter-spacing:.1em;color:var(--muted-light)">HEAD OF BD • REGIONAL EPC CONTRACTOR</div>
  </section>

  <section class="sec light" style="top:783px;height:144px;background:#f6f3ee">
    <div class="a center" style="top:19px;height:4px"><span class="eyebrow" style="background:none;border:0">FAQ</span></div>
    <h2 class="a h center" style="top:27px;font-size:7.4px">Questions, answered.</h2>
    <div class="a" style="left:89px;top:43px;width:143px;height:23px;background:#fff;border:.3px solid #e6dfd4;border-radius:2px;padding:3px 4px">
      <div class="row" style="justify-content:space-between;font-size:2.6px;font-weight:600">What’s included in the platform?<span style="width:5px;height:5px;border-radius:50%;background:var(--orange);color:#fff;font-size:3px;display:flex;align-items:center;justify-content:center">–</span></div>
      <div class="tiny" style="color:var(--muted);margin-top:3px">Industry intelligence, supplier directory, tender hub, project database, legal framework, market reports, ownership data and compliance tools — all in one workspace.</div>
    </div>
    <div class="faq" style="top:70px;height:11px">How current is the data?<span>⌄</span></div>
    <div class="faq" style="top:85px;height:11px">Do you offer language support?<span>⌄</span></div>
    <div class="faq" style="top:99px;height:11px">Can we integrate Tarnovex with our systems?<span>⌄</span></div>
    <div class="faq" style="top:114px;height:11px">How is the data verified?<span>⌄</span></div>
  </section>

  <section class="sec dark" style="top:927px;height:195px">
    <div class="photo" role="img" aria-label="Silhouette of a refinery skyline under a purple dusk sky" style="left:0;top:0;width:100%;height:100px;background:radial-gradient(ellipse at 50% 30%,rgba(140,80,160,.35),transparent 60%),linear-gradient(180deg,#2c1a4c,#1d1236)"></div>
    <div class="a center" style="top:23px;height:4px"><span class="eyebrow">Ready when you are</span></div>
    <h2 class="a h" style="left:60px;width:202px;top:34px;text-align:center;font-size:9.6px;line-height:1.3">Unlock Mozambique’s <span class="hl">energy opportunities.</span></h2>
    <p class="a p" style="left:100px;width:122px;top:61px;text-align:center;font-size:2.4px">Join the operators, investors and suppliers using Tarnovex to navigate the world’s most exciting energy frontier.</p>
    <div class="a row" style="left:0;width:100%;top:75px;justify-content:center;gap:3px"><span class="btn btn-o">Register Today →</span><span class="btn btn-g">Book consultation ↗</span></div>

    <div class="a" style="left:57px;top:117px;width:66px">
      <div class="logo"><i></i>Tarnovex</div>
      <p class="tiny" style="color:var(--muted-light);margin-top:3px">The enterprise intelligence platform for Mozambique’s Oil &amp; Gas sector. Verified data, trusted analysis, decisions that scale.</p>
      <div style="font-size:1.6px;letter-spacing:.1em;color:var(--muted-light);margin-top:3px">SUBSCRIBE TO INSIGHTS</div>
      <div class="row" style="margin-top:1.5px;height:6px;border-radius:3px;background:rgba(255,255,255,.06);border:.3px solid var(--line-dark);justify-content:space-between;padding-left:2px"><span class="tiny" style="color:var(--muted-light);font-size:1.8px">you@company.com</span><span class="btn btn-o" style="height:5px;font-size:1.8px;padding:0 2.5px">Subscribe</span></div>
      <div class="row" style="gap:2px;margin-top:4px"><span class="tag" style="font-size:1.6px">English</span><span class="tag" style="font-size:1.6px">Português</span><span class="tag" style="font-size:1.6px">Français</span></div>
    </div>
    <div class="a" style="left:143px;top:117px;width:130px;height:40px">
      <div class="fcol" style="left:0"><b>PLATFORM</b>Intelligence<br>Tenders<br>Suppliers<br>Projects<br>Legal</div>
      <div class="fcol" style="left:32px"><b>COMPANY</b>About<br>Careers<br>Press<br>Contact</div>
      <div class="fcol" style="left:64px"><b>RESOURCES</b>Newsroom<br>Reports<br>Help center<br>API docs</div>
      <div class="fcol" style="left:96px"><b>LEGAL</b>Privacy<br>Terms<br>Cookies<br>Security</div>
    </div>
    <div class="a" style="left:57px;top:175px;width:207px;border-top:.3px solid var(--line-dark)"></div>
    <div class="a tiny" style="left:57px;top:178px;font-size:1.8px;color:var(--muted-light)">© 2026 Tarnovex. All rights reserved.</div>
    <div class="a tiny" style="left:226px;top:178px;font-size:1.8px;color:var(--muted-light)">◍ Maputo • Pemba • London</div>
  </section>
</div>

</body>
</html>
```